Healthy Meal Delivery Website Needs to be updated, current, fresh and modern

Hi there,

The current website i have is super old and outdated.

I would like a beautiful modern site that has all the same content as the previous except with a a new, modern and trustworthy feel.

The current website is https://tovalplatefresh.com/

Target Market(s)

Health Conscious Young Professionals

Industry/Entity Type

Food Service

Font styles to use
Sans Serif

Requirements
Must have
• Modern Trustworthy feel
Should not have
• Anything out dated or cheesy or scammy

```html
<!DOCTYPE html>
<html lang="en">
<head>
<meta charset="utf-8">
<title>Toval Plate Fresh – Diet Meals Delivered</title>
<link href="https://fonts.googleapis.com/css2?family=Arimo:wght@400;700&family=Delius&family=Poppins:wght@400;500;600&display=swap" rel="stylesheet">
<style>
:root{
  --yellow:#ece81c;
  --lime:#cde21e;
  --blue:#1a8fd6;
  --blue-dark:#1478bd;
  --teal:#2aa59a;
  --green:#4cae3c;
  --ink:#333;
  --muted:#555;
  --light:#f4f4f4;
  --white:#fff;
  --body-font:"Arimo",Arial,sans-serif;
}
*{box-sizing:border-box;margin:0;padding:0}
html,body{width:1200px;height:3103px;overflow:hidden}
body{font-family:"Poppins",Arial,sans-serif;color:var(--ink);background:var(--white);position:relative}
p{font-family:var(--body-font)}
.display{font-family:"Delius","Comic Neue",sans-serif}
section,header,footer{position:relative;width:1200px;overflow:hidden}
.abs{position:absolute}
.btn{display:inline-flex;align-items:center;justify-content:center;background:var(--blue);color:var(--white);border-radius:24px;font-weight:600;text-decoration:none}

/* top bar */
.topbar{position:relative;height:48px;background:var(--yellow);font-size:12px;color:var(--blue-dark);font-family:var(--body-font)}
.topbar .contact{left:86px;top:16px}
.topbar .signup{left:944px;top:10px;width:80px;height:28px;background:var(--blue);color:#fff;font-size:12px;font-weight:600;display:flex;align-items:center;justify-content:center}
.topbar .login{left:1032px;top:10px;width:80px;height:28px;border:1.5px solid var(--blue-dark);color:var(--blue-dark);font-size:12px;font-weight:600;display:flex;align-items:center;justify-content:center}

/* header */
.site-header{height:90px;background:var(--white)}
.brand{left:86px;top:30px;display:flex;align-items:center;gap:10px;font-family:"Delius",sans-serif;font-size:22px;color:var(--blue-dark)}
.brand .dot{width:26px;height:26px;border-radius:50%;background:var(--yellow)}
.nav{right:86px;top:36px;display:flex;gap:38px;font-size:15px;color:#333}
.nav .active{color:var(--blue)}

/* hero */
.hero{height:577px;background:linear-gradient(90deg,#dfe3e6,#f2f3f4 60%,#e9ecec)}
.hero-photo{left:0;top:0;width:1200px;height:577px;background:radial-gradient(ellipse at 30% 45%,#e8c8a4 0,#d9c1a3 14%,rgba(230,232,232,0) 38%),radial-gradient(ellipse at 40% 82%,#c84b3a 0,rgba(200,75,58,0) 18%),radial-gradient(ellipse at 1110px 420px,#7bb341 0,rgba(123,179,65,0) 10%)}
.hero h1{left:738px;top:70px;font-size:40px;font-weight:400;color:var(--blue)}
.hero ul{left:742px;top:145px;list-style:none;font-size:14px;color:#555}
.hero li{display:flex;align-items:center;gap:20px;height:43px}
.hero li svg{flex:none}
.hero .btn{left:744px;top:328px;width:136px;height:46px;font-size:15px}
.hero .wave{left:0;bottom:0}

/* intro */
.intro{height:575px;text-align:center}
.intro h2{font-family:"Delius",sans-serif;font-weight:400;font-size:23px;color:#444;margin-top:37px}
.intro h3{font-family:"Delius",sans-serif;font-weight:400;font-size:28px;color:var(--blue);margin-top:8px}
.intro .lead{width:700px;margin:36px auto 0;font-size:12.5px;line-height:26px;color:#555}
.features{display:flex;justify-content:center;margin-top:68px}
.feature{width:258px;display:flex;flex-direction:column;align-items:center}
.feature svg{height:90px}
.feature h4{font-family:"Delius",sans-serif;font-weight:400;font-size:17px;color:var(--blue);margin-top:10px}
.feature p{font-size:12px;line-height:25px;color:#555;width:244px;margin-top:12px;min-height:75px}
.feature .btn{width:110px;height:36px;font-size:11.5px;margin-top:18px;flex:none}

/* diet band */
.diet{height:600px}
.diet-bg{left:0;top:0}
.monitor{left:116px;top:58px;width:496px;height:292px;border-radius:10px;background:#1f1f1f;padding:16px}
.monitor .screen{width:100%;height:100%;background:radial-gradient(ellipse at 45% 50%,#e8dcc2 0,#b9a57b 35%,#6b4a2f 70%,#3a2a20 100%)}
.monitor-base{left:116px;top:350px;width:496px;height:40px;background:linear-gradient(#dcdcdc,#bcbcbc);border-radius:0 0 8px 8px}
.monitor-stand{left:316px;top:390px;width:96px;height:48px;background:linear-gradient(#cfcfcf,#a9a9a9);clip-path:polygon(12% 0,88% 0,100% 100%,0 100%)}
.diet-copy{left:675px;top:112px;width:440px;color:#fff}
.diet-copy h2{font-family:"Delius",sans-serif;font-weight:400;font-size:32px;margin-bottom:22px}
.diet-copy h5{font-family:"Delius",sans-serif;font-weight:400;font-size:17px;color:var(--yellow);letter-spacing:.5px}
.diet-copy p{font-size:11.5px;line-height:25px;margin:2px 0 12px}

/* menu */
.menu{height:593px;text-align:center}
.menu h2{font-family:"Delius",sans-serif;font-weight:400;font-size:28px;color:var(--blue);margin-top:40px}
.menu .lead{font-size:12px;color:#555;margin-top:18px}
.menu-items{display:flex;justify-content:center;gap:128px;margin-top:48px}
.menu-item{width:218px}
.menu-item .plate{width:218px;height:218px;border-radius:50%;border:6px solid #e6e6e6}
.menu-item h4{font-family:"Delius",sans-serif;font-weight:400;font-size:20px;color:var(--blue);margin-top:24px}
.menu-item p{font-size:12px;line-height:25px;color:#555;width:290px;margin:20px 0 0 -36px}
.menu-item a{display:block;font-size:13px;color:var(--blue);font-weight:500;margin-top:20px;text-decoration:none}

/* testimonial */
.testimonial{height:294px;background:var(--light)}
.quote{left:208px;top:58px;width:530px;font-size:12px;line-height:25px;color:#555}
.quote .mark{font-family:Georgia,serif;font-size:30px;color:#aaa;position:absolute}
.author{left:210px;top:196px;font-family:"Delius",sans-serif;font-size:18px;color:var(--blue)}
.posted{left:210px;top:224px;font-size:12px;color:#555;font-family:var(--body-font)}
.avatar{left:810px;top:46px;width:196px;height:196px;border-radius:50%;border:6px solid #ddd;background:radial-gradient(circle at 50% 40%,#c9a58a,#8a5a3e 70%,#5a3a28)}

/* footer */
.site-footer{height:326px;background:var(--blue);color:#fff}
.footer-brand{left:86px;top:42px;display:flex;align-items:center;gap:10px;font-family:"Delius",sans-serif;font-size:22px}
.footer-brand .dot{width:26px;height:26px;border-radius:50%;background:var(--yellow)}
.footer-about{left:86px;top:100px;width:300px;font-size:11.5px;line-height:25px}
.footer-col-title{font-family:"Delius",sans-serif;font-size:20px;color:var(--yellow)}
.quick{left:448px;top:50px}
.quick ul{list-style:none;display:grid;grid-template-columns:148px 100px;font-size:11.5px;line-height:32px;margin-top:24px;font-family:var(--body-font)}
.newsletter{left:740px;top:50px;width:345px}
.newsletter p{font-size:11.5px;line-height:25px;margin-top:24px}
.subscribe{margin-top:14px;display:flex;height:46px}
.subscribe span{flex:1;background:#fff;color:#555;font-size:12px;display:flex;align-items:center;padding-left:20px;font-family:var(--body-font)}
.subscribe b{width:50px;background:var(--yellow);display:flex;align-items:center;justify-content:center}
.copyright{left:86px;top:285px;font-size:10.5px;font-family:var(--body-font)}
.footer-links{right:86px;top:285px;font-size:10.5px;display:flex;gap:12px;font-family:var(--body-font)}
</style>
</head>
<body>

<div class="topbar">
  <div class="contact abs">&#9742;&nbsp; Phone : (416) 555-0182 &nbsp;|&nbsp;&nbsp; &#9993; Email : sales@tovalplatefresh.com</div>
  <div class="signup abs">SIGN UP</div>
  <div class="login abs">LOGIN</div>
</div>

<header class="site-header">
  <div class="brand abs"><span class="dot"></span>Toval Plate Fresh</div>
  <nav class="nav abs">
    <span class="active">Home</span><span>Toval Meal Plans</span><span>Menu</span><span>Pricing</span><span>About</span><span>Press</span><span>Contact</span>
  </nav>
</header>

<section class="hero">
  <div class="hero-photo abs" role="img" aria-label="Smiling woman in a bright kitchen eating a cherry tomato beside a bowl of fresh salad"></div>
  <h1 class="abs display">Toval Plate Fresh</h1>
  <ul class="abs">
    <li><svg width="14" height="12" viewBox="0 0 14 12"><path d="M1 6l4 4 8-9" fill="none" stroke="#1a8fd6" stroke-width="2.4"/></svg>Real food you'll love to eat</li>
    <li><svg width="14" height="12" viewBox="0 0 14 12"><path d="M1 6l4 4 8-9" fill="none" stroke="#1a8fd6" stroke-width="2.4"/></svg>Portion controlled meals to maximize your weight loss</li>
    <li><svg width="14" height="12" viewBox="0 0 14 12"><path d="M1 6l4 4 8-9" fill="none" stroke="#1a8fd6" stroke-width="2.4"/></svg>No grocery shopping, cooking or cleaning required</li>
    <li><svg width="14" height="12" viewBox="0 0 14 12"><path d="M1 6l4 4 8-9" fill="none" stroke="#1a8fd6" stroke-width="2.4"/></svg>Freshly prepared by our in house chefs</li>
  </ul>
  <a class="btn abs">Read More</a>
  <svg class="wave abs" width="1200" height="160" viewBox="0 0 1200 160">
    <path d="M0 150 C250 40 520 60 700 80 C900 100 1080 80 1200 150 L1200 160 L0 160Z" fill="#fff"/>
    <path d="M0 120 C220 40 420 50 600 70" fill="none" stroke="#ece81c" stroke-width="14"/>
    <path d="M0 140 C230 60 440 70 640 80" fill="none" stroke="#1a8fd6" stroke-width="6"/>
  </svg>
</section>

<section class="intro">
  <h2>The Toval Diet Delivers Diet Meals</h2>
  <h3>To Your Door In Toronto, Gta &amp; Montreal</h3>
  <p class="lead">Our fresh and delicious diet meals and snacks are made with only the best natural ingredients that nourish your body.&nbsp; Why not let us prepare your meals while you lose the weight?</p>
  <div class="features">
    <div class="feature">
      <svg viewBox="0 0 90 90" width="90"><path d="M45 26c-10-8-30-4-30 20 0 20 14 34 30 30 16 4 30-10 30-30 0-24-20-28-30-20z" fill="none" stroke="#1a8fd6" stroke-width="4"/><path d="M45 26c0-8 4-14 10-18" stroke="#4cae3c" stroke-width="4" fill="none"/><path d="M47 20c2-10 12-14 20-12-2 10-12 14-20 12z" fill="#b8d82a"/></svg>
      <h4>Healthy</h4>
      <p>The Toval Diet is a great way to ensure you are eating all the nutrients you need, nothing your body doesn't need.</p>
      <a class="btn">READ MORE</a>
    </div>
    <div class="feature">
      <svg viewBox="0 0 90 90" width="90"><g fill="#ece81c"><rect x="14" y="16" width="12" height="10"/><rect x="14" y="38" width="12" height="10"/><rect x="14" y="60" width="12" height="10"/></g><g fill="#1a8fd6"><rect x="32" y="18" width="44" height="6"/><rect x="32" y="40" width="44" height="6"/><rect x="32" y="62" width="44" height="6"/></g><g fill="#2aa59a"><rect x="14" y="28" width="62" height="4"/><rect x="14" y="50" width="62" height="4"/></g></svg>
      <h4>Choice</h4>
      <p>You can choose your own meals from over 100 tasty entrees, desserts and meals fo snack foods.</p>
      <a class="btn">READ MORE</a>
    </div>
    <div class="feature">
      <svg viewBox="0 0 90 90" width="90"><path d="M18 74C14 40 40 14 76 14 78 50 54 76 18 74z" fill="#cfe4a0" stroke="#2aa59a" stroke-width="4"/><path d="M18 74L66 24" stroke="#2aa59a" stroke-width="3"/></svg>
      <h4>Fresh</h4>
      <p>All of our meals are real food, freshly prepared by our in-house expert chefs.an choose your meals online</p>
      <a class="btn">READ MORE</a>
    </div>
    <div class="feature">
      <svg viewBox="0 0 90 90" width="90"><rect x="10" y="14" width="70" height="60" rx="6" fill="none" stroke="#1a8fd6" stroke-width="4"/><path d="M10 28h70" stroke="#2aa59a" stroke-width="4"/><circle cx="45" cy="51" r="11" fill="none" stroke="#1a8fd6" stroke-width="4"/><circle cx="45" cy="51" r="4" fill="#ece81c"/></svg>
      <h4>Customized</h4>
      <p>Your meals will be delivered fresh to your door, customized for your unique body type and level of activity.</p>
      <a class="btn">READ MORE</a>
    </div>
  </div>
</section>

<section class="diet">
  <svg class="diet-bg abs" width="1200" height="600" viewBox="0 0 1200 600">
    <defs><linearGradient id="dietGrad" x1="0" y1="0" x2="1" y2="0"><stop offset="0" stop-color="#d6e21c"/><stop offset=".45" stop-color="#8fcc2a"/><stop offset=".7" stop-color="#2aa59a"/><stop offset="1" stop-color="#1a8fd6"/></linearGradient></defs>
    <path d="M0 100 C200 60 420 130 620 110 C800 90 920 20 1040 10 C1120 5 1170 30 1200 60 L1200 600 L0 600Z" fill="url(#dietGrad)"/>
    <path d="M0 100 C200 60 420 130 620 110 C800 90 920 20 1040 10 C1120 5 1170 30 1200 60" fill="none" stroke="#1a8fd6" stroke-width="6"/>
  </svg>
  <div class="monitor abs"><div class="screen" role="img" aria-label="Plate of fresh rice noodle salad with vegetables and peanuts"></div></div>
  <div class="monitor-base abs"></div>
  <div class="monitor-stand abs"></div>
  <div class="diet-copy abs">
    <h2>The Toval Diet</h2>
    <h5>WHAT YOU GET</h5>
    <p>Toval Diet Delivery provides you with 3 fresh daily meals and 3 snacks delivered to your doorstep before 6am.</p>
    <h5>SELECTION</h5>
    <p>Choose your meals from over 100 delicious entrees, snacks and desserts.</p>
    <h5>LUXURY</h5>
    <p>Enjoy the luxury of having your own personal chef and nutritionist prepare Toval Diet meals for you.</p>
    <h5>WHAT IS PHASE 1?</h5>
    <p>Phase 1 is the stricter phase that eliminates bad carbs and processed foods no sugar, candy, pasta or bread.</p>
    <h5>WHAT IS PHASE 2?</h5>
    <p>Phase 2 reintroduces certain healthy carbs into your diet - whole grains, rice and potatoes, providing you with a greater variety of meals.</p>
  </div>
</section>

<section class="menu">
  <h2>Select From Over 100 Menu Items</h2>
  <p class="lead">You can choose your own meals from over 100 tasty entrees, desserts and snack foods. You can choose your meals online</p>
  <div class="menu-items">
    <div class="menu-item">
      <div class="plate" role="img" aria-label="Grilled chicken breast" style="background:radial-gradient(circle,#e6b070,#b8743a 60%,#7a4a22)"></div>
      <h4>01.Breakfast</h4>
      <p>You can choose your own meals from over 100 tasty entrees, desserts and snack foods. You can choose your meals online,</p>
      <a>Read More</a>
    </div>
    <div class="menu-item">
      <div class="plate" role="img" aria-label="Fresh lettuce wrap roll" style="background:radial-gradient(circle,#f3efd8,#b8d68a 55%,#6e9a3c)"></div>
      <h4>02.Snack</h4>
      <p>You can choose your own meals from over 100 tasty entrees, desserts and snack foods. You can choose your meals online,</p>
      <a>Read More</a>
    </div>
    <div class="menu-item">
      <div class="plate" role="img" aria-label="Grilled meat skewers" style="background:radial-gradient(circle,#8a5a3a,#5a3422 55%,#2e1a12)"></div>
      <h4>03.Lunch</h4>
      <p>You can choose your own meals from over 100 tasty entrees, desserts and snack foods. You can choose your meals online,</p>
      <a>Read More</a>
    </div>
  </div>
  <svg class="abs" style="left:38px;top:165px" width="24" height="100" viewBox="0 0 24 100"><path d="M22 2L2 50 22 98" fill="none" stroke="#bbb" stroke-width="2"/></svg>
  <svg class="abs" style="right:38px;top:165px" width="24" height="100" viewBox="0 0 24 100"><path d="M2 2L22 50 2 98" fill="none" stroke="#bbb" stroke-width="2"/></svg>
</section>

<section class="testimonial">
  <svg class="abs" style="left:38px;top:95px" width="24" height="100" viewBox="0 0 24 100"><path d="M22 2L2 50 22 98" fill="none" stroke="#ccc" stroke-width="2"/></svg>
  <svg class="abs" style="right:38px;top:95px" width="24" height="100" viewBox="0 0 24 100"><path d="M2 2L22 50 2 98" fill="none" stroke="#ccc" stroke-width="2"/></svg>
  <p class="quote abs"><span class="mark" style="left:-20px;top:-16px">&ldquo;</span>I thought I went to heaven when I tasted the tofu kebabs with wild rice, but then I realized I was still on earth. It was the most delicious tofu dish I ever tasted! Also, I like and enjoy all your shrimp reci pes, and the new shrimp with fennel was no exception. Please give my thanks to your chefs! They I tasted the tofu kebabs with wild rice made great changes.<span class="mark" style="margin-left:4px;position:relative;top:10px">&rdquo;</span></p>
  <div class="author abs">Lorna</div>
  <div class="posted abs">Posted On 07 May 2018</div>
  <div class="avatar abs" role="img" aria-label="Customer portrait"></div>
</section>

<footer class="site-footer">
  <div class="footer-brand abs"><span class="dot"></span>Toval Plate Fresh</div>
  <p class="footer-about abs">Toval is the Toronto &amp; Montreal Diet Delivery program based on the Toval Diet, healthy carbs and the right fatsWe provide you with 3 fresh meals, 2 snacks and a dessert delivered to your door before 6am.Try our delivery plan and start Toval weight loss now!</p>
  <div class="quick abs">
    <div class="footer-col-title">Quick Links</div>
    <ul><li>Home</li><li>About</li><li>Toval Meal Plans</li><li>Press</li><li>Menu</li><li>Contact</li><li>Pricing</li></ul>
  </div>
  <div class="newsletter abs">
    <div class="footer-col-title">Newsletter</div>
    <p>Sed ut perspiciatis unde omnis iste natus error sit voluptatem accusantium doloremque laudantium</p>
    <div class="subscribe"><span>Enter Your Email id</span><b><svg width="18" height="16" viewBox="0 0 18 16"><path d="M1 8L17 1 13 15 8 10z" fill="#1478bd"/></svg></b></div>
  </div>
  <div class="copyright abs">© Copyright-2018 Toval Plate Fresh.All rights reserved.</div>
  <div class="footer-links abs"><span>HOME</span>|<span>MEAL PLANS</span>|<span>PRICING</span>|<span>CONTACT</span>|<span>SIGN UP</span>|<span>LOGIN</span>|<span>PRIVACY</span>|<span>TERMS OF USE</span></div>
</footer>

</body>
</html>
```